KRT Engineering Business Card Design

We’re looking for an elegant, clean, and timeless business card design that communicates experience, capability, and reliability.

KRT Engineering was established in 1995 , we are a Government Contracting company providing Professional Services to the Office of Frontier Affairs, Harbor Protection and the Vantage Collective. Our capabilities include: Acquisition & Program Management; Intelligence & Security Operations; Cyber, IT & Network Operations; Lifecycle Logistics & Asset Readiness; C5ISR Systems Engineering & Sustainment.

We want the card to reflect a straightforward, confident approach to business. The design should feel polished and professional without being flashy or overly corporate.

Design Direction
Clean, sophisticated, and uncluttered
Elegant but understated
Strong typography and thoughtful spacing
A timeless aesthetic rather than something overly trendy
Confident and established, with a sense of substance
Easy to read and practical in a real-world business setting

The overall impression should be: “These are experienced professionals who know what they’re doing, do what they say, and can be relied upon.”

We’re open to creative interpretations. The finished card should feel distinctive through its typography, proportions, layout, and attention to detail rather than through excessive graphics or visual effects.

We’re looking for a design that would make a potential client immediately feel that they’re dealing with a capable, trustworthy, and established company.

Company Colors: Navy and Gold/Yellow (but you do not need to use these colors on the card)
Company Name: KRT Engineering Associates, Inc. (known as KRT Engineering)
Website: krtengineering.com
Company Logo: Navy & Gold (other variations attached)

```html
<!DOCTYPE html>
<html lang="en">
<head>
<meta charset="utf-8">
<title>KRT Engineering Business Card</title>
<link href="https://fonts.googleapis.com/css2?family=Arimo:wght@400;700&display=swap" rel="stylesheet">
<style>
  :root {
    --backdrop: #1d1d1f;
    --card-light: #f3f3f2;
    --navy: #1f2a5f;
    --ink: #2a2a2e;
    --white: #f4f4f4;
  }
  * { margin: 0; padding: 0; box-sizing: border-box; }
  html, body { width: 1200px; height: 1059px; overflow: hidden; }
  body {
    background: var(--backdrop);
    font-family: "Arimo", Arial, sans-serif;
    position: relative;
  }
  .card {
    position: absolute;
    border-radius: 17px;
    box-shadow: 0 10px 26px rgba(0,0,0,0.55);
  }
  .card--front {
    left: 257px; top: 89px; width: 687px; height: 390px;
    background: var(--card-light);
  }
  .card--back {
    left: 254px; top: 547px; width: 693px; height: 393px;
    background: var(--navy);
  }
  .wordmark {
    position: absolute;
    left: 0; right: 0;
    text-align: center;
    font-weight: 700;
    letter-spacing: -1px;
    line-height: 1;
  }
  .card--front .wordmark {
    top: 92px;
    font-size: 80px;
    color: var(--navy);
  }
  .card--back .wordmark {
    top: 158px;
    font-size: 117px;
    color: var(--white);
  }
  .identity {
    position: absolute;
    right: 368px;
    top: 256px;
    text-align right;
    text-align: right;
  }
  .identity__name {
    font-size: 25px;
    font-weight: 700;
    color: var(--navy);
    line-height: 1.1;
  }
  .identity__title {
    font-size: 18px;
    color: var(--ink);
    margin-top: 3px;
  }
  .divider {
    position: absolute;
    left: 343px;
    top: 244px;
    width: 1.5px;
    height: 79px;
    background: var(--navy);
  }
  .contacts {
    position: absolute;
    left: 367px;
    top: 236px;
    list-style: none;
  }
  .contacts li {
    display: flex;
    align-items: center;
    height: 31px;
    font-size: 18.5px;
    color: var(--ink);
  }
  .contacts svg {
    width: 13px; height: 13px;
    margin-right: 9px;
    fill: var(--navy);
    flex-shrink: 0;
  }
</style>
</head>
<body>
  <section class="card card--front">
    <div class="wordmark">KRT</div>
    <div class="identity">
      <p class="identity__name">Maren L. Whitfield</p>
      <p class="identity__title">Principal Engineer</p>
    </div>
    <div class="divider"></div>
    <ul class="contacts">
      <li>
        <svg viewBox="0 0 24 24" aria-hidden="true"><path d="M6.6 10.8a15.1 15.1 0 0 0 6.6 6.6l2.2-2.2a1 1 0 0 1 1-.25 11.4 11.4 0 0 0 3.6.6 1 1 0 0 1 1 1V20a1 1 0 0 1-1 1A17 17 0 0 1 3 4a1 1 0 0 1 1-1h3.5a1 1 0 0 1 1 1c0 1.25.2 2.45.6 3.6a1 1 0 0 1-.25 1z"/></svg>
        (555) 438-2716
      </li>
      <li>
        <svg viewBox="0 0 24 24" aria-hidden="true"><path d="M2 9l10-7 10 7v12H2zm2 2v8h16v-8l-8 5z"/></svg>
        m.w@krtengineering.com
      </li>
      <li>
        <svg viewBox="0 0 24 24" aria-hidden="true"><path d="M12 2a10 10 0 1 0 0 20 10 10 0 0 0 0-20zm-1 17.9A8 8 0 0 1 4.1 11H7v2l2 2v2l2 1zm6.9-2.5A2 2 0 0 0 16 16h-1v-3l-4-1V9h3V6h2a8 8 0 0 1 1.9 11.4z"/></svg>
        krtengineering.com
      </li>
    </ul>
  </section>

  <section class="card card--back">
    <div class="wordmark">KRT</div>
  </section>
</body>
</html>
```